Security based company delivering High Risk Training to Law Enforcement Agencies Worldwide.

We need a Web design for a company doing business in Washington D.C. We deliver High Risk Training to Law Enforcement Agencies throughout the world. Our focus is on Improvised Explosive Devices. We train Bomb Technicians and First Responders in all aspects relating to bombings and criminal incidents globally.
Updates

Reason: We have uploaded our logo. Thank you.

Target Market(s)

Military and Law Enforcement Personnel from around the world.

Industry/Entity Type

Business

Requirements
Should not have
• Do not include cartoon like characters.

```html
<!DOCTYPE html>
<html lang="en">
<head>
<meta charset="utf-8">
<title>Vantrel International – High Risk Training</title>
<link href="https://fonts.googleapis.com/css2?family=Arimo:wght@400;700&family=Source+Sans+3:wght@400;600&display=swap" rel="stylesheet">
<style>
:root{
  --red:#c8171e;
  --red-bright:#d4232a;
  --ink:#222;
  --grey-text:#555;
  --muted:#6b6b6b;
  --line:#d9d9d9;
  --card-border:#d6d6d6;
  --btn-dark:#3b3b3b;
  --footer:#2e2e2e;
  --footer-bottom:#222;
  --footer-text:#c9c9c9;
  --paper:#fff;
  --sand:#cdb89a;
  --sand-light:#e4d6c0;
  --fire:#f2a23a;
}
*{box-sizing:border-box;margin:0;padding:0}
html,body{width:1183px;height:1200px;overflow:hidden;background:var(--paper)}
body{position:relative;font-family:"Arimo",Arial,sans-serif;color:var(--ink)}
.abs{position:absolute}
.photo{background:linear-gradient(135deg,var(--sand-light),var(--sand) 60%,#b89d78)}
.photo.fire{background:linear-gradient(100deg,#e8ded0 0%,#d9cdbd 45%,var(--fire) 70%,#f6d27a 85%,#d9c6a6 100%)}
.photo.dust{background:linear-gradient(180deg,#d9cfc4 0%,#c9b9a5 55%,#b59c7c 100%)}
.photo.suit{background:linear-gradient(120deg,#5d6a4a 0%,#8a8f78 45%,#cfc7ba 75%,#bfae94 100%)}

/* feature cards */
.card{top:0;width:211px;height:210px;border:1px solid var(--card-border);border-top:none;border-radius:0 0 4px 4px;background:var(--paper);text-align:center}
.card.active{background:#f6f6f6}
.card .photo{height:56px}
.card h3{font-family:"Source Sans 3",sans-serif;font-weight:400;color:var(--red);font-size:18px;margin-top:10px}
.card p{font-size:13px;line-height:21.6px;color:var(--ink);text-align:left;padding:0 9px 0 9px;margin-top:4px}
.btn{display:inline-block;margin-top:9px;padding:3px 6px;border-radius:3px;background:var(--btn-dark);color:#fff;font-size:13px}
.card.active .btn{background:var(--red-bright)}

.rule{left:137px;width:909px;height:1px;background:var(--line)}
.section-title{left:0;width:1183px;text-align:center;font-family:"Arimo",sans-serif;font-size:22px;color:var(--muted)}
.section-title em{font-style:normal;color:var(--red);font-size:25px}

.arrow{top:258px;width:27px;height:27px;border-radius:2px;display:flex;align-items:center;justify-content:center}

/* video */
.video-frame{left:137px;top:301px;width:464px;height:302px;border:1px solid var(--card-border);padding:5px}
.video-frame .photo{width:100%;height:262px;position:relative}
.controls{height:28px;background:linear-gradient(#4a4a4a,#232323);position:relative}

.post{left:625px;width:910px}
.post .thumb{left:625px;width:164px;height:90px;border:1px solid var(--card-border);padding:5px}
.post .thumb div{width:100%;height:100%}
.post-text{left:799px;width:247px}
.post-text h4{font-family:"Source Sans 3",sans-serif;font-weight:600;color:var(--red);font-size:16px}
.post-text p{font-size:12.5px;line-height:16.5px;color:var(--grey-text);text-align:justify;margin-top:2px}
.post-text a{display:block;font-size:12px;font-weight:700;color:var(--ink);margin-top:1px;text-decoration:none;letter-spacing:.3px}

/* testimonial */
.avatar{left:136px;top:688px;width:98px;height:98px;border-radius:50%;border:1px solid var(--red);padding:5px}
.avatar div{width:100%;height:100%;border-radius:50%;background:radial-gradient(circle at 50% 40%,#d9c3b0,#8d8d8d 70%,#5a5a5a)}
.quote{left:250px;top:714px;width:795px;text-align:center;font-size:13px;line-height:21.6px;color:var(--ink)}
.quote-mark{font-family:Georgia,serif;font-weight:700;font-size:30px;line-height:1;color:var(--ink)}
.author{left:0;width:1183px;top:786px;text-align:center;font-size:12px;font-weight:700;color:var(--ink)}
.author span{color:var(--red)}
.dot{top:817px;width:14px;height:14px;border-radius:50%;background:#cfcfcf}
.dot.on{background:var(--red-bright)}

/* footer */
.footer-band{left:0;top:869px;width:1183px;height:7px;background:var(--red)}
.footer{left:0;top:876px;width:1183px;height:274px;background:var(--footer)}
.footer-bottom{left:0;top:1150px;width:1183px;height:50px;background:var(--footer-bottom);color:var(--footer-text);font-size:11px;text-align:center;line-height:50px}
.col h5{font-family:"Source Sans 3",sans-serif;font-weight:400;font-size:21px;color:var(--red)}
.col ul{list-style:none;margin-top:8px}
.col li{font-size:13px;line-height:19.2px;color:var(--footer-text);padding-left:17px;position:relative}
.col li::before{content:"";position:absolute;left:2px;top:6px;width:5px;height:5px;border-top:2px solid var(--red);border-right:2px solid var(--red);transform:rotate(45deg)}
.col.news li{line-height:19px;margin-bottom:20px;width:234px;text-align:justify}
.social{display:flex;align-items:center;gap:14px;font-size:13px;color:var(--footer-text);height:45px}
.social i{width:26px;height:26px;border-radius:50%;display:block}
</style>
</head>
<body>

<!-- feature cards -->
<div class="card abs" style="left:137px">
  <div class="photo fire" role="img" aria-label="Car exploding during a training demonstration"></div>
  <h3>Consectetuer adipiscing</h3>
  <p>Lorem ipsum dolor sit amet, con­sectetuer adipiscing elit, sed diam nonummy nibh.</p>
  <span class="btn">Read More</span>
</div>
<div class="card abs active" style="left:370px">
  <div class="photo dust" role="img" aria-label="Blast debris rising from desert ground"></div>
  <h3>Consectetuer adipiscing</h3>
  <p>Lorem ipsum dolor sit amet, con­sectetuer adipiscing elit, sed diam nonummy nibh.</p>
  <span class="btn">Read More</span>
</div>
<div class="card abs" style="left:601px">
  <div class="photo suit" role="img" aria-label="Bomb technician in protective suit with robot"></div>
  <h3>Consectetuer adipiscing</h3>
  <p>Lorem ipsum dolor sit amet, con­sectetuer adipiscing elit, sed diam nonummy nibh.</p>
  <span class="btn">Read More</span>
</div>
<div class="card abs" style="left:834px">
  <div class="photo dust" role="img" aria-label="Controlled detonation on open range"></div>
  <h3>Consectetuer adipiscing</h3>
  <p>Lorem ipsum dolor sit amet, con­sectetuer adipiscing elit, sed diam nonummy nibh.</p>
  <span class="btn">Read More</span>
</div>

<div class="rule abs" style="top:239px"></div>

<!-- video blog -->
<h2 class="section-title abs" style="top:254px">Video <em>Blog</em></h2>
<div class="arrow abs" style="left:983px;background:#333">
  <svg width="10" height="12" viewBox="0 0 10 12"><path d="M7 1 2 6l5 5" stroke="#fff" stroke-width="2.4" fill="none"/></svg>
</div>
<div class="arrow abs" style="left:1019px;background:var(--red)">
  <svg width="10" height="12" viewBox="0 0 10 12"><path d="M3 1l5 5-5 5" stroke="#fff" stroke-width="2.4" fill="none"/></svg>
</div>

<div class="video-frame abs">
  <div class="photo fire" role="img" aria-label="Video still of a car burning after a test explosion">
    <svg class="abs" style="left:180px;top:80px" width="100" height="100" viewBox="0 0 100 100">
      <circle cx="50" cy="50" r="45" fill="rgba(255,255,255,.25)" stroke="rgba(255,255,255,.75)" stroke-width="6"/>
      <rect x="36" y="30" width="9" height="40" rx="3" fill="rgba(255,255,255,.8)"/>
      <rect x="55" y="30" width="9" height="40" rx="3" fill="rgba(255,255,255,.8)"/>
    </svg>
  </div>
  <div class="controls">
    <svg width="452" height="28" viewBox="0 0 452 28">
      <circle cx="16" cy="14" r="10" fill="#111" stroke="#777"/>
      <path d="M13 9v10l8-5z" fill="#ddd"/>
      <rect x="34" y="12" width="270" height="4" rx="2" fill="#111"/>
      <rect x="34" y="12" width="146" height="4" rx="2" fill="var(--red)"/>
      <circle cx="180" cy="14" r="6" fill="#ccc" stroke="#555"/>
      <text x="310" y="18" font-size="9" fill="#ddd" font-family="Arimo,sans-serif">04:25</text>
      <path d="M342 11h4l5-4v14l-5-4h-4z" fill="#ccc"/>
      <rect x="360" y="12" width="54" height="4" rx="2" fill="#111"/>
      <rect x="360" y="12" width="34" height="4" rx="2" fill="var(--red)"/>
      <rect x="392" y="7" width="4" height="14" rx="1" fill="#ccc"/>
      <path d="M428 8h5M428 8v5M446 8h-5M446 8v5M428 21h5M428 21v-5M446 21h-5M446 21v-5" stroke="#ccc" stroke-width="1.6"/>
    </svg>
  </div>
</div>

<div class="thumb abs post" style="top:301px;left:625px;width:164px;height:90px;border:1px solid var(--card-border);padding:5px">
  <div class="photo fire" style="height:100%" role="img" aria-label="Car exploding"></div>
</div>
<div class="post-text abs" style="top:302px">
  <h4>Consectetuer Adipiscing elit</h4>
  <p>Lorem ipsum dolor sit amet, consectetuer adipiscing elit, sed diam nonummy nibh euismod tincidunt ut laoreet.</p>
  <a href="#">Read More</a>
</div>

<div class="abs" style="top:409px;left:625px;width:164px;height:90px;border:1px solid var(--card-border);padding:5px">
  <div class="photo dust" style="height:100%" role="img" aria-label="Debris thrown up on a test range"></div>
</div>
<div class="post-text abs" style="top:410px">
  <h4>Consectetuer Adipiscing elit</h4>
  <p>Lorem ipsum dolor sit amet, consectetuer adipiscing elit, sed diam nonummy nibh euismod tincidunt ut laoreet.</p>
  <a href="#">Read More</a>
</div>

<div class="abs" style="top:517px;left:625px;width:164px;height:90px;border:1px solid var(--card-border);padding:5px">
  <div class="photo suit" style="height:100%" role="img" aria-label="Technician in bomb suit approaching a device"></div>
</div>
<div class="post-text abs" style="top:518px">
  <h4>Consectetuer Adipiscing elit</h4>
  <p>Lorem ipsum dolor sit amet, consectetuer adipiscing elit, sed diam nonummy nibh euismod tincidunt ut laoreet.</p>
  <a href="#">Read More</a>
</div>

<div class="rule abs" style="top:634px"></div>

<!-- testimonials -->
<h2 class="section-title abs" style="top:646px">Client <em>Testimonials</em></h2>
<div class="avatar abs"><div role="img" aria-label="Portrait of the client"></div></div>
<span class="quote-mark abs" style="left:240px;top:700px">&ldquo;</span>
<p class="quote abs">Lorem ipsum dolor sit amet, consectetuer adipiscing elit, sed diam nonummy nibh euismod tincidunt ut laoreet dolore magna aliquam erat volutpat. Ut wisi enim ad minim veniam, quis nostrud exerci tation ullamcorper suscipit lobortis nisl ut aliquip ex ea commodo consequat. Duis autem vel eum iriure dolor in hendrerit in vulputate velit esse molestie consequat <b>&rdquo;</b></p>
<p class="author abs"><span>Quis nostrud exerci Tation,</span> Aus</p>
<span class="dot abs" style="left:549px"></span>
<span class="dot abs on" style="left:572px"></span>
<span class="dot abs" style="left:595px"></span>
<span class="dot abs" style="left:619px"></span>

<div class="rule abs" style="top:850px"></div>

<!-- footer -->
<div class="footer-band abs"></div>
<footer class="footer abs">
  <div class="col abs" style="left:137px;top:14px">
    <h5>Main Links</h5>
    <ul>
      <li>Home</li><li>About Us</li><li>Lorem Ipsum</li><li>Consectetuer</li>
      <li>Adipiscing Elit</li><li>Nostrud Exerci Tation</li><li>Consectetuer Adipiscing</li><li>Tation Ullamco</li>
    </ul>
  </div>
  <div class="col abs" style="left:384px;top:14px">
    <h5>Categories</h5>
    <ul>
      <li>Lorem ipsum dolo</li><li>consectetuer adipiscing</li><li>Lorem Ipsum</li><li>Quis nostrud exerci tation</li>
      <li>Adipiscing Elit</li><li>Nostrud Exerci Tation</li><li>Consectetuer Adipiscing</li><li>Eum iriure dolor in hendrerit</li>
    </ul>
  </div>
  <div class="col news abs" style="left:624px;top:14px">
    <h5>News &amp; Events</h5>
    <ul>
      <li>Lorem ipsum dolor sit amet, consect­etuer adipiscing elit, sed diam non­ummy nibh euismod tincidunt .</li>
      <li>Lorem ipsum dolor sit amet, consect­etuer adipiscing elit, sed diam non­ummy nibh euismod tincidunt .</li>
      <li>Lorem ipsum dolor sit amet, consect­etuer adipiscing elit, sed diam non­ummy nibh euismod tincidunt.</li>
    </ul>
  </div>
  <div class="col abs" style="left:935px;top:14px">
    <h5>Follow Us On</h5>
    <div style="margin-top:6px">
      <div class="social"><i style="background:#3b5a99"></i>friendwall</div>
      <div class="social"><i style="background:#3c9ad6"></i>chirpline</div>
      <div class="social"><i style="background:#d34836"></i>circleplus</div>
      <div class="social"><i style="background:#d8342b"></i>clipstream</div>
    </div>
  </div>
</footer>
<div class="footer-bottom abs">© 2014 Vantrel International. All Rights Reserved.</div>

</body>
</html>
```